Redesign a Start-Up Dating Website

Website: https://morvelique.com.
Make sure the design has an island style theme.
I would like the 7 pages of my website to have a new and professional look. I want the same colors to remain, but I want a creative look for all the pages. This is a dating website that is in the startup stage. So, I want to give my entire website a custom makeover. I want something that will stand out from the other dating sites. Something that will attract more people to want to use my services, and hopefully get new members.
Target Market(s)
Dating
Industry/Entity Type
Dating
Coding
Coded - Design and coding required
Number of Pages Required
5+ page
Font styles to use
Other font styles liked:
- Decorative, San Serif
Requirements
Must have
- The design must have the original colors and a stylish font to go along. The design must be creative, welcoming, and professional. I would like an island style theme for the website. This is a dating website so make sure that the design is tailored to that aspect.
Nice to have
- It would be nice to have a decorative font and a professional style on all the pages. Make sure the design will be mobile responsive and friendly for all the pages on the website.
Should not have
- The design should not be bland and uncreative.

```html
<!DOCTYPE html>
<html lang="en">
<head>
<meta charset="utf-8">
<title>Morvelique – Search</title>
<link rel="stylesheet" href="https://fonts.googleapis.com/css2?family=Raleway:wght@600;700;800&family=Open+Sans:wght@400;600;700&display=swap">
<style>
:root{
  --orange:#f7931e;
  --teal:#3fb2a0;
  --ink:#2b2b2b;
  --text:#444;
  --muted:#666;
  --line:#bdbdbd;
  --field-border:#a9a9a9;
  --footer-bg:#ececec;
  --white:#fff;
}
*{box-sizing:border-box;margin:0;padding:0}
html,body{width:964px;height:1200px;overflow:hidden;background:var(--white)}
body{position:relative;font-family:"Open Sans",Arial,sans-serif;color:var(--text)}
.top-bar{position:absolute;left:0;top:0;width:964px;height:3px;background:linear-gradient(90deg,var(--teal),var(--orange))}
.site-header{position:absolute;left:0;top:3px;width:964px;height:71px;background:var(--white);box-shadow:0 2px 4px rgba(0,0,0,.25);z-index:2}
.brand{position:absolute;left:77px;top:13px;display:flex;align-items:center;gap:5px}
.brand-dot{width:44px;height:44px;border-radius:50%;background:var(--orange)}
.brand-name{font-family:"Raleway",sans-serif;font-weight:800;font-size:26px;color:var(--teal)}
.main-nav{position:absolute;left:305px;top:28px;width:480px;display:flex;justify-content:space-between;font-family:"Raleway",sans-serif;font-weight:700;font-size:12.5px;color:var(--ink)}
.main-nav .active{color:var(--orange)}
.login-btn{position:absolute;left:803px;top:17px;width:82px;height:34px;border-radius:17px;background:var(--orange);color:var(--white);font-family:"Raleway",sans-serif;font-weight:700;font-size:13px;display:flex;align-items:center;justify-content:center;gap:5px}
.hero{position:absolute;left:0;top:74px;width:964px;height:228px;background:linear-gradient(180deg,#7a7390 0%,#a497a8 40%,#6d7590 70%,#3f4f6a 100%)}
.hero-title{position:absolute;left:0;top:80px;width:964px;text-align:center;font-family:"Raleway",sans-serif;font-weight:800;font-size:56px;color:var(--white);letter-spacing:-1px}
.breadcrumb{position:absolute;left:79px;top:318px;font-family:"Raleway",sans-serif;font-weight:700;font-size:12px;color:var(--ink)}
.breadcrumb .sep{margin:0 6px}
.breadcrumb .current{color:var(--orange)}
.rule{position:absolute;left:79px;top:347px;width:806px;height:1px;background:var(--line)}
.heading-art{position:absolute;left:289px;top:404px;width:59px;height:50px;border-radius:24px;background:linear-gradient(135deg,var(--teal) 0%,var(--teal) 45%,var(--orange) 100%)}
.section-title{position:absolute;left:363px;top:416px;font-family:"Raleway",sans-serif;font-weight:800;font-size:23px;color:var(--ink)}
.search-form .row{position:absolute;left:0;width:964px;height:39px}
.field-label{position:absolute;right:714px;top:0;height:39px;line-height:39px;font-weight:600;font-size:13px;color:var(--ink);text-align:right;white-space:nowrap}
.select{position:absolute;top:0;height:39px;border:1px solid var(--field-border);background:var(--white);font-size:11px;color:var(--muted);line-height:37px;padding-left:13px}
.select::after{content:"";position:absolute;right:0;top:0;width:46px;height:37px;border-left:1px solid var(--field-border)}
.select .caret{position:absolute;right:19px;top:16px;width:0;height:0;border-left:4px solid transparent;border-right:4px solid transparent;border-top:5px solid #555}
.search-btn{position:absolute;left:426px;top:882px;width:113px;height:44px;border-radius:22px;background:var(--orange);color:var(--white);font-weight:700;font-size:14px;display:flex;align-items:center;justify-content:center}
.site-footer{position:absolute;left:0;top:1002px;width:964px;height:198px;background:var(--footer-bg)}
.footer-line{height:4px;background:linear-gradient(90deg,var(--teal),var(--orange))}
.contact-item{position:absolute;display:flex;align-items:center;gap:14px;font-size:12px;color:var(--text);line-height:19px}
.icon-ring{width:35px;height:35px;border:1px solid #aaa;border-radius:50%;display:flex;align-items:center;justify-content:center;flex:none}
.footer-links{position:absolute;left:0;top:97px;width:964px;text-align:center;font-size:12.5px;color:var(--muted)}
.footer-links span{margin:0 6px}
.footer-rule{position:absolute;left:79px;top:137px;width:806px;height:1px;background:#ccc}
.copyright{position:absolute;left:80px;top:158px;font-size:11px;color:var(--muted)}
.social{position:absolute;left:786px;top:154px;display:flex;gap:5px}
.social-link{width:30px;height:30px;border:1px solid #999;border-radius:50%;display:flex;align-items:center;justify-content:center}
.social-link::after{content:"";width:8px;height:8px;border-radius:50%;background:var(--orange)}
</style>
</head>
<body>
<div class="top-bar"></div>
<header class="site-header">
  <div class="brand"><span class="brand-dot"></span><span class="brand-name">Morvelique</span></div>
  <nav class="main-nav">
    <span>HOME</span><span class="active">SEARCH</span><span>MEMBERS</span><span>EXTRAS</span><span>ABOUT</span><span>PREMIUM</span><span>CONTACT</span>
  </nav>
  <div class="login-btn">
    <svg width="9" height="11" viewBox="0 0 9 11"><rect x="0" y="5" width="9" height="6" rx="1" fill="#fff"/><path d="M2 5V3.5a2.5 2.5 0 0 1 5 0V5" stroke="#fff" stroke-width="1.5" fill="none"/></svg>
    LOGIN
  </div>
</header>

<section class="hero" role="img" aria-label="Couple holding hands on a beach at sunset">
  <h1 class="hero-title">SEARCH</h1>
</section>

<div class="breadcrumb">HOME<span class="sep">&gt;&gt;</span><span class="current">SEARCH</span></div>
<div class="rule"></div>

<div class="heading-art" role="img" aria-label="Teal and orange hearts illustration"></div>
<h2 class="section-title">FIND YOUR PERFECT MATCH</h2>

<form class="search-form">
  <div class="row" style="top:505px"><span class="field-label">I AM:</span><div class="select" style="left:295px;width:486px">Man<i class="caret"></i></div></div>
  <div class="row" style="top:565px"><span class="field-label" style="right:717px">SEEKING A:</span><div class="select" style="left:295px;width:486px">Man<i class="caret"></i></div></div>
  <div class="row" style="top:624px"><span class="field-label">AGE:</span><div class="select" style="left:295px;width:236px">18<i class="caret"></i></div><div class="select" style="left:545px;width:236px">99<i class="caret"></i></div></div>
  <div class="row" style="top:684px"><span class="field-label">COUNTRY:</span><div class="select" style="left:295px;width:486px">Select Country<i class="caret"></i></div></div>
  <div class="row" style="top:745px"><span class="field-label">ONLINE ONLY</span><div class="select" style="left:295px;width:486px">No<i class="caret"></i></div></div>
  <div class="row" style="top:805px"><span class="field-label">WITH PICTURES ONLY</span><div class="select" style="left:295px;width:486px">No Preference<i class="caret"></i></div></div>
  <div class="search-btn">SEARCH</div>
</form>

<footer class="site-footer">
  <div class="footer-line"></div>
  <div class="contact-item" style="left:185px;top:34px">
    <span class="icon-ring"><svg width="10" height="14" viewBox="0 0 10 14"><path d="M5 0a5 5 0 0 0-5 5c0 4 5 9 5 9s5-5 5-9a5 5 0 0 0-5-5z" fill="var(--orange)"/><circle cx="5" cy="5" r="1.8" fill="#fff"/></svg></span>
    <div>Morvelique Dating<br>Contact | Morvelique | Dating Easy</div>
  </div>
  <div class="contact-item" style="left:449px;top:34px">
    <span class="icon-ring"><svg width="13" height="13" viewBox="0 0 13 13"><path d="M3 0l2 3-1.5 1.5c.8 2 2.5 3.7 4.5 4.5L9.5 7.5l3 2-1 3C6 12 1 7 .5 1.5z" fill="var(--orange)"/></svg></span>
    <div>1 555 010 2040</div>
  </div>
  <div class="contact-item" style="left:614px;top:34px">
    <span class="icon-ring"><svg width="15" height="11" viewBox="0 0 15 11"><rect width="15" height="11" rx="1" fill="var(--orange)"/><path d="M1 1l6.5 5L14 1" stroke="#fff" stroke-width="1.3" fill="none"/></svg></span>
    <div>contact@morvelique.com</div>
  </div>
  <div class="footer-links">Morvelique<span>|</span>About<span>|</span>Contact<span>|</span>Login<span>|</span>Members<span>|</span>Premium<span>|</span>Register<span>|</span>Search</div>
  <div class="footer-rule"></div>
  <div class="copyright">Copyrights © 2017, Morvelique. All rights reserved.</div>
  <div class="social">
    <span class="social-link" role="img" aria-label="Social network link"></span>
    <span class="social-link" role="img" aria-label="Social network link"></span>
    <span class="social-link" role="img" aria-label="Social network link"></span>
  </div>
</footer>
</body>
</html>
```